real esate business card with company logo and name

we need a business card design for a real esate company

The company name is Walsh & Brand Pty Ltd, and we have our logo designed and will upload. We want classic or moden feel. Black or white background. looks more textured. Should include folowinginformations
Owen Walsh and Lucy Brand
Sales Agents & Onsite Manager
p: 07 5948 2063
F: 07 5948 2174
M:0431 857 219
3/42 Marlow Crescent, FERNLEA QLD 4213

We want this business card looks professonal. Thank you in advance.

Industry/Entity Type

Real Estate Agent

Contact Information for Business Card

Owen Walsh and Lucy Brand
Onsite Manager & Sales Agents
p: 07 5948 2063
M:0431 857 219

Font styles to use
Serif

Colors
000000
fbfbfb
333333
959595

Requirements
Must have
• company logo and name, black or white back ground

```html
<!DOCTYPE html>
<html lang="en">
<head>
<meta charset="utf-8">
<title>Walsh &amp; Brand Pty Ltd – Business Card</title>
<link href="https://fonts.googleapis.com/css2?family=Source+Sans+3:wght@400;600&display=swap" rel="stylesheet">
<style>
  :root {
    --backdrop: #2e2e2e;
    --card-light: #f7f7f7;
    --card-dark: #4a4a4a;
    --band-dark: #5a5a5a;
    --band-light: #a6a6a6;
    --ink: #333333;
    --ink-soft: #959595;
    --mark: #6b6b6b;
    --white: #fbfbfb;
  }
  * { margin: 0; padding: 0; box-sizing: border-box; }
  html, body {
    width: 1200px; height: 750px; overflow: hidden;
    background: var(--backdrop);
    font-family: "Source Sans 3", sans-serif;
  }
  .canvas { position: relative; width: 1200px; height: 750px; }
  .card {
    position: absolute; top: 228px;
    width: 462px; height: 263px; overflow: hidden;
  }
  .card--front { left: 124px; background: var(--card-light); }
  .card--back { left: 618px; background: var(--card-dark); }
  .card__bands { position: absolute; inset: 0; }

  .brand {
    position: absolute; left: 0; width: 218px; top: 0; height: 263px;
    display: flex; flex-direction: column; align-items: center; justify-content: center; gap: 14px;
  }
  .brand__square { width: 34px; height: 34px; background: var(--mark); }
  .brand__name {
    font-size: 11px; font-weight: 600; letter-spacing: 0.06em;
    color: var(--ink); text-transform: uppercase;
  }
  .divider {
    position: absolute; left: 218px; top: 76px; width: 1px; height: 136px;
    background: #cfcfcf;
  }
  .details { position: absolute; left: 234px; top: 76px; color: var(--ink); }
  .details__names { font-size: 17px; font-weight: 600; line-height: 20px; }
  .details__role { font-size: 12px; color: var(--ink-soft); line-height: 16px; margin-top: 1px; }
  .details__address { font-size: 11px; line-height: 14px; margin-top: 10px; }
  .contact { list-style: none; margin-top: 10px; }
  .contact li {
    display: flex; align-items: center; gap: 7px;
    font-size: 11px; line-height: 17.5px;
  }
  .contact svg { width: 12px; height: 12px; fill: var(--ink); }

  .back-brand {
    position: absolute; inset: 0;
    display: flex; align-items: center; justify-content: center;
  }
  .back-brand__name {
    font-size: 34px; font-weight: 600; letter-spacing: 0.06em;
    color: var(--white); text-transform: uppercase;
  }
</style>
</head>
<body>
<main class="canvas">
  <section class="card card--front" aria-label="Business card front">
    <svg class="card__bands" viewBox="0 0 462 263" aria-hidden="true">
      <polygon points="0,0 462,0 462,12 60,12 0,58" fill="var(--band-dark)"/>
      <polygon points="462,204 396,250 462,250" fill="var(--band-light)"/>
      <rect x="0" y="250" width="462" height="13" fill="var(--band-light)"/>
    </svg>
    <div class="brand">
      <span class="brand__square"></span>
      <span class="brand__name">Walsh &amp; Brand Pty Ltd.</span>
    </div>
    <div class="divider"></div>
    <div class="details">
      <h1 class="details__names">Owen Walsh &amp; Lucy Brand</h1>
      <p class="details__role">Sales Agents &amp; Onsite Manager</p>
      <p class="details__address">3/42 Marlow Crescent<br>FERNLEA QLD 4213</p>
      <ul class="contact">
        <li>
          <svg viewBox="0 0 24 24" aria-label="Phone"><path d="M6.6 10.8a15 15 0 0 0 6.6 6.6l2.2-2.2c.3-.3.7-.4 1-.2 1.1.4 2.3.6 3.6.6.6 0 1 .4 1 1V20c0 .6-.4 1-1 1A17 17 0 0 1 3 4c0-.6.4-1 1-1h3.5c.6 0 1 .4 1 1 0 1.3.2 2.5.6 3.6.1.3 0 .7-.2 1z"/></svg>
          07 5948 2063
        </li>
        <li>
          <svg viewBox="0 0 24 24" aria-label="Mobile"><path d="M7 1h10a2 2 0 0 1 2 2v18a2 2 0 0 1-2 2H7a2 2 0 0 1-2-2V3a2 2 0 0 1 2-2zm0 3v15h10V4z"/></svg>
          0431 857 219
        </li>
        <li>
          <svg viewBox="0 0 24 24" aria-label="Fax"><path d="M7 3h10v5H7zM3 9h18v9h-3v3H6v-3H3zm5 7v3h8v-3z"/></svg>
          07 5948 2174
        </li>
      </ul>
    </div>
  </section>

  <section class="card card--back" aria-label="Business card back">
    <div class="back-brand">
      <span class="back-brand__name">Walsh &amp; Brand</span>
    </div>
  </section>
</main>
</body>
</html>
```